Car transport business

We need a new business card design. Attached is our old card sample. I would just like to adjust the logo colors (blue and red) to be brighter. I changed my name to the brighter red and the word dispatcher to a brighter blue as an example. But you can adjust those colors further. And then perhaps you can use the same colors for the card design but use your imagination.

As a suggestion so the card stands out I would like to add a clip art of car carrier truck. Attached are examples of that as well

```html
<!DOCTYPE html>
<html lang="en">
<head>
<meta charset="utf-8">
<title>Northline Haul – Business Card</title>
<link href="https://fonts.googleapis.com/css2?family=Exo+2:ital,wght@0,600;0,800;1,800&family=Roboto:wght@400;500&display=swap" rel="stylesheet">
<style>
  :root {
    --stage: #2c2c2c;
    --brand-blue: #1f74bd;
    --brand-red: #ea1c24;
    --plum: #7a4a7e;
    --white: #ffffff;
    --ink: #151515;
  }
  html, body {
    margin: 0;
    width: 1200px;
    height: 866px;
    overflow: hidden;
    background: var(--stage);
  }
  .stage {
    position: relative;
    width: 1200px;
    height: 866px;
  }
  .card {
    position: absolute;
    top: 284px;
    width: 520px;
    height: 298px;
    overflow: hidden;
    box-shadow: 0 14px 30px rgba(0,0,0,.45);
  }
  .card--front { left: 60px; background: var(--white); }
  .card--back { left: 620px; }
  .card__art {
    position: absolute;
    inset: 0;
    width: 100%;
    height: 100%;
  }
  .truck-illustration {
    position: absolute;
    left: 14px;
    top: 26px;
    width: 200px;
    height: 120px;
    background: linear-gradient(180deg, #2a2a2a, #0e0e0e);
    border-radius: 6px;
  }
  .wordmark {
    position: absolute;
    font-family: "Exo 2", sans-serif;
    font-weight: 800;
    letter-spacing: 1px;
    white-space: nowrap;
  }
  .wordmark__dot {
    display: inline-block;
    border-radius: 50%;
    vertical-align: middle;
    margin-right: 8px;
  }
  .tagline {
    position: absolute;
    font-family: "Exo 2", sans-serif;
    font-weight: 600;
    text-transform: uppercase;
    white-space: nowrap;
  }
  .card--front .wordmark { left: 250px; top: 70px; font-size: 27px; color: var(--brand-blue); }
  .card--front .wordmark__dot { width: 14px; height: 14px; background: var(--brand-red); }
  .card--front .tagline { left: 272px; top: 106px; font-size: 9.5px; letter-spacing: 2.2px; color: var(--brand-blue); }
  .holder {
    position: absolute;
    left: 28px;
    top: 178px;
    color: var(--white);
  }
  .holder__name {
    font-family: "Exo 2", sans-serif;
    font-weight: 800;
    font-style: italic;
    font-size: 26px;
    letter-spacing: 1px;
    margin: 0;
  }
  .holder__role {
    font-family: "Roboto", sans-serif;
    font-size: 12px;
    letter-spacing: 1px;
    margin: 2px 0 0;
  }
  .contact {
    position: absolute;
    left: 250px;
    top: 246px;
    margin: 0;
    padding: 0;
    list-style: none;
    font-family: "Roboto", sans-serif;
    font-size: 12.5px;
    line-height: 16px;
    color: var(--white);
  }
  .contact li { display: flex; align-items: center; gap: 7px; }
  .contact svg { width: 11px; height: 11px; fill: var(--white); }
  .card--back .wordmark {
    left: 0; right: 0; top: 118px;
    text-align: center;
    font-size: 36px;
    color: var(--white);
  }
  .card--back .wordmark__dot { width: 18px; height: 18px; background: var(--white); }
  .card--back .tagline {
    left: 0; right: 0; top: 166px;
    text-align: center;
    font-size: 11px;
    letter-spacing: 3px;
    color: var(--white);
  }
</style>
</head>
<body>
<main class="stage">

  <section class="card card--front" aria-label="Business card front">
    <svg class="card__art" viewBox="0 0 520 298" aria-hidden="true">
      <polygon class="band band--blue" points="0,120 520,250 520,298 0,298" fill="var(--brand-blue)"/>
      <polygon class="stripe stripe--red" points="200,152 520,230 520,238 200,160" fill="var(--brand-red)"/>
    </svg>
    <div class="truck-illustration" role="img" aria-label="Car carrier truck clip art loaded with cars"></div>
    <div class="wordmark"><span class="wordmark__dot"></span>NORTHLINE HAUL</div>
    <div class="tagline">The Auto Transport Professionals</div>
    <div class="holder">
      <p class="holder__name">RAVI DENNER</p>
      <p class="holder__role">DIAPATCHER</p>
    </div>
    <ul class="contact">
      <li><svg viewBox="0 0 12 12"><path d="M2.5 1l2 2.3-1 1.2a6 6 0 0 0 4 4l1.2-1 2.3 2-1 1.5C6 11 1 6 1 2z"/></svg>555-210-4830</li>
      <li><svg viewBox="0 0 12 12"><rect x="3" y="1" width="6" height="3"/><rect x="1" y="4.5" width="10" height="4.5" rx="1"/><rect x="3" y="8" width="6" height="3"/></svg>555-210-4831</li>
      <li><svg viewBox="0 0 12 12"><path d="M1 2.5h10v7H1z M1 2.5l5 4 5-4" stroke="#1f74bd" stroke-width=".8"/></svg>northlinehaul@mail.example</li>
    </ul>
  </section>

  <section class="card card--back" aria-label="Business card back">
    <svg class="card__art" viewBox="0 0 520 298" aria-hidden="true">
      <defs>
        <linearGradient id="back-fill" x1="0" y1="1" x2="1" y2="0">
          <stop offset="0" stop-color="var(--brand-blue)"/>
          <stop offset=".5" stop-color="var(--plum)"/>
          <stop offset="1" stop-color="var(--brand-red)"/>
        </linearGradient>
      </defs>
      <rect width="520" height="298" fill="url(#back-fill)"/>
      <path class="sweep" d="M0 70 C150 40 330 30 470 70 C500 80 515 100 520 115 L520 95 C500 60 450 40 380 32 C250 20 120 35 0 55z" fill="#ffffff" opacity=".08"/>
      <path class="sweep" d="M0 230 C140 200 320 200 520 240 L520 262 C330 225 150 222 0 250z" fill="#1f74bd" opacity=".35"/>
      <path class="sweep" d="M430 40 C480 55 510 80 520 110 L520 130 C505 95 475 70 430 55z" fill="#ffffff" opacity=".12"/>
    </svg>
    <div class="wordmark"><span class="wordmark__dot"></span>NORTHLINE HAUL</div>
    <div class="tagline">The Auto Transport Professionals</div>
  </section>

</main>
</body>
</html>
```